Need a developer to develop and design my virtual employee recruitment solution website.

I need the entire website developed, from the design, the navigation, the contents of the website, etc. I need a professional looking website yet have that modern look. You can suggest the best fonts, color combinations to use. I need the site to be SEO friendly. I also want high quality stock photos to be used on the website. I wanted to achieve a similar website like this https://remotehelperpool.example/.

Target Market(s)

Ecommerce Entrepreneurs, Businessmen, Cartwell and Bazorra Sellers.

Industry/Entity Type

Professional Service

Coding

Coded - Design and coding required

Number of Pages Required

5+ page

Font styles to use
Sans Serif

Requirements
Must have
• I wanted it to have pages like this https://remotehelperpool.example/
Nice to have
• open for any recommendation you can suggest
Should not have
• Cannot think of any. You can suggest your own here

```html
<!DOCTYPE html>
<html lang="en">
<head>
<meta charset="utf-8">
<title>Remote Harbor – Virtual Staffing</title>
<link href="https://fonts.googleapis.com/css2?family=Montserrat:wght@500;600;700;800&family=Arimo:ital,wght@0,400;0,700;1,400&display=swap" rel="stylesheet">
<style>
:root{
  --blue:#0f62c9;
  --blue-deep:#0a4fae;
  --dark:#232323;
  --ink:#262626;
  --text:#3a3a3a;
  --grey-bg:#ebebeb;
  --white:#ffffff;
  --sky:#cfe6fb;
}
*{box-sizing:border-box;margin:0;padding:0}
html,body{width:1200px;height:3649px;overflow:hidden}
body{position:relative;background:var(--white);font-family:"Arimo",Arial,sans-serif;color:var(--text)}
.abs{position:absolute}

/* nav */
.topnav{position:absolute;left:0;top:0;width:1200px;height:48px;background:var(--blue);z-index:5}
.topnav ul{position:absolute;left:157px;top:0;display:flex;list-style:none;height:48px}
.topnav li{font-family:"Montserrat",sans-serif;font-weight:700;font-size:14px;color:var(--white);line-height:48px;padding:0 17px}
.topnav li.active{background:var(--dark);padding:0 22px}
.topnav .search{position:absolute;left:1058px;top:15px}

/* hero */
.hero{position:absolute;left:0;top:0;width:1200px;height:701px;overflow:hidden}
.hero-photo{position:absolute;left:0;top:48px;width:1200px;height:620px;
  background:linear-gradient(100deg,#e9eef3 0%,#dfe5ea 35%,#9fb0c3 60%,#d8dde3 80%,#c6ced7 100%)}
.hero-swoosh{position:absolute;left:0;top:520px;width:1200px;height:181px}
.brand-name{position:absolute;font-family:"Montserrat",sans-serif;font-weight:800;font-size:36px;line-height:1.02;color:var(--blue)}
.hero .brand-name{left:172px;top:145px}
.hero-title{position:absolute;left:166px;top:328px;font-family:"Montserrat",sans-serif;font-weight:800;font-size:70px;line-height:66px;color:var(--white);letter-spacing:1px}
.btn-hero{position:absolute;left:171px;top:483px;width:277px;height:44px;border-radius:22px;background:var(--blue);color:var(--white);
  font-family:"Montserrat",sans-serif;font-weight:700;font-size:13px;display:flex;align-items:center;justify-content:center}
.call{position:absolute;left:913px;top:76px;display:flex;gap:12px;align-items:flex-start}
.call p{font-family:"Montserrat",sans-serif;font-weight:700;font-size:19px;color:var(--dark);line-height:22px}

/* sections */
.sec-title{position:absolute;left:0;width:1200px;text-align:center;font-family:"Montserrat",sans-serif;font-weight:700;font-size:30px;color:var(--ink)}
.rule{position:absolute;left:565px;width:70px;height:4px;background:var(--blue)}
.welcome-copy{position:absolute;left:330px;top:881px;width:540px;text-align:center;font-size:14px;line-height:22.5px;color:var(--text)}
.portrait-deco{position:absolute;left:255px;top:1015px}
.get-title{position:absolute;left:667px;top:1042px;font-family:"Montserrat",sans-serif;font-weight:700;font-size:19px;line-height:23px;color:var(--ink)}
.get-rule{position:absolute;left:667px;top:1100px;width:70px;height:3px;background:var(--blue)}
.benefits{position:absolute;left:667px;top:1129px;list-style:none;width:360px}
.benefits li{position:relative;padding-left:25px;font-size:14px;line-height:17px;color:var(--text);margin-bottom:20.5px}
.benefits li svg{position:absolute;left:0;top:1px}

.va-band{position:absolute;left:0;top:1403px;width:1200px;height:641px;background:var(--blue)}
.va-band .sec-title{color:var(--white);top:70px}
.va-band .rule{background:var(--white);top:129px}
.va-copy{position:absolute;left:171px;top:190px;width:415px;color:var(--white);font-size:14px;line-height:22.5px}
.va-copy p{margin-bottom:22.5px}
.btn-outline{position:absolute;display:flex;align-items:center;justify-content:center;border:2px solid var(--white);border-radius:24px;
  color:var(--white);font-family:"Montserrat",sans-serif;font-weight:700;font-size:14px}
.va-band .btn-outline{left:173px;top:532px;width:183px;height:46px}
.va-art{position:absolute;left:612px;top:205px;width:508px;height:436px;border-radius:48% 52% 0 0 / 40% 46% 0 0;
  background:linear-gradient(160deg,#e3f1fd 0%,var(--sky) 55%,#9fcaf1 100%)}

.why{position:absolute;left:0;top:2044px;width:1200px;height:722px;background:var(--grey-bg)}
.why .sec-title{color:var(--blue);top:104px}
.why .rule{top:165px}
.pill{position:absolute;width:309px;height:48px;border-radius:24px;background:var(--blue);color:var(--white);
  font-family:"Montserrat",sans-serif;font-weight:700;font-size:14px;display:flex;align-items:center;padding-left:19px}
.pill.active{background:var(--dark)}
.pill.center{left:397px;width:406px;justify-content:center;padding-left:0}
.why-dial{position:absolute;left:455px;top:228px;width:290px;height:290px}
.why-dial p{position:absolute;left:55px;top:138px;width:180px;text-align:center;font-size:13.5px;line-height:21px;color:var(--text)}

.test-card{position:absolute;top:2944px;height:235px;background:var(--white);border:1px solid #d9d9d9;padding:40px 24px 0 26px}
.test-card.featured{border-color:#e6eef9;box-shadow:0 0 22px rgba(15,98,201,.22);padding:40px 48px 0 46px}
.test-card .quote{font-family:"Montserrat",sans-serif;font-weight:800;font-size:54px;line-height:30px;color:var(--blue);height:34px}
.test-card p{font-style:italic;font-size:12.4px;line-height:21px;color:var(--text);margin-top:8px}
.test-card h4{font-family:"Montserrat",sans-serif;font-weight:600;font-size:17px;color:var(--ink);margin-top:12px;margin-left:-6px}
.dots{position:absolute;left:563px;top:3203px;display:flex;gap:5px}
.dots span{width:13px;height:13px;border-radius:50%;background:#cfcfcf}
.dots span.on{background:var(--dark)}

.footer{position:absolute;left:0;top:3280px;width:1200px;height:369px}
.footer .brand-name{left:172px;top:160px;color:var(--white);font-size:32px}
.foot-links{position:absolute;top:165px;list-style:none}
.foot-links li{font-family:"Montserrat",sans-serif;font-size:14px;color:var(--white);line-height:24px}
.footer .btn-outline{left:891px;width:132px;height:36px;font-size:12px;border-radius:18px}
.foot-rule{position:absolute;left:170px;top:314px;width:858px;height:1px;background:rgba(255,255,255,.6)}
.copyright{position:absolute;left:170px;top:334px;font-size:11.5px;color:var(--white)}
.social{position:absolute;left:950px;top:333px;display:flex;gap:16px}
.social span{width:13px;height:13px;border-radius:50%;background:var(--white)}
</style>
</head>
<body>

<header class="hero">
  <div class="hero-photo" role="img" aria-label="Stock photo of a smiling woman in glasses working on a laptop at a bright office desk"></div>
  <svg class="hero-swoosh" viewBox="0 0 1200 181" preserveAspectRatio="none" aria-hidden="true">
    <path d="M0 40 Q520 170 1200 70 L1200 181 L0 181Z" fill="#0f62c9"/>
    <path d="M0 95 Q560 215 1200 80 L1200 181 L0 181Z" fill="#232323"/>
    <path d="M0 110 Q580 225 1200 105 L1200 181 L0 181Z" fill="#ffffff"/>
  </svg>
  <div class="brand-name">REMOTE<br>HARBOR</div>
  <h1 class="hero-title">REMOTE<br>HARBOR</h1>
  <a class="btn-hero">REQUEST A PHONE CONSULTATION</a>
  <div class="call">
    <svg width="40" height="40" viewBox="0 0 24 24" aria-hidden="true"><path fill="#0f62c9" d="M6.6 10.8a15.2 15.2 0 0 0 6.6 6.6l2.2-2.2c.3-.3.7-.4 1-.2 1.1.4 2.3.6 3.6.6.6 0 1 .4 1 1V20c0 .6-.4 1-1 1A17 17 0 0 1 3 4c0-.6.4-1 1-1h3.5c.6 0 1 .4 1 1 0 1.3.2 2.5.6 3.6.1.3 0 .7-.2 1z"/></svg>
    <p>CALL US:<br>555 014 2290</p>
  </div>
</header>

<nav class="topnav">
  <ul>
    <li class="active">HOME</li><li>ABOUT US</li><li>SERVICES OFFERED</li><li>PRICING</li><li>TESTIMONIALS</li><li>FAQS</li><li>CONTACT US</li><li>BLOG</li>
  </ul>
  <svg class="search" width="16" height="16" viewBox="0 0 16 16" aria-hidden="true"><circle cx="6.5" cy="6.5" r="5" fill="none" stroke="#fff" stroke-width="2"/><path d="M10.5 10.5 15 15" stroke="#fff" stroke-width="2"/></svg>
</nav>

<section class="welcome">
  <h2 class="sec-title" style="top:798px">WELCOME TO REMOTE HARBOR</h2>
  <div class="rule" style="top:859px"></div>
  <p class="welcome-copy">Tired of being stuck in your 9-5 cubicle job? Exhausted from commuting to and from the office? Want to spend more time with your family? We've got you covered. RemoteHarbor is a virtual staffing company that helps freelancers and virtual assistants find their perfect work-from-home job. We have a pool of clients from all over the world who are all looking for talented virtual assistants.</p>
  <svg class="portrait-deco" width="340" height="340" viewBox="0 0 340 340" aria-hidden="true">
    <circle cx="180" cy="170" r="166" fill="#232323"/>
    <circle cx="195" cy="170" r="142" fill="#ffffff"/>
    <rect x="320" y="90" width="30" height="160" fill="#ffffff"/>
    <circle cx="170" cy="166" r="158" fill="#0f62c9"/>
    <path d="M170 8 A158 158 0 0 1 328 166 L300 166 A130 130 0 0 0 170 36Z" fill="#232323"/>
    <circle cx="175" cy="164" r="135" fill="#ffffff"/>
  </svg>
  <div class="abs" role="img" aria-label="Stock photo of a smiling man in glasses talking on the phone" style="left:295px;top:1047px;width:270px;height:270px;border-radius:50%;background:linear-gradient(150deg,#6f8a78 0%,#9fb2a8 40%,#4f6f96 75%,#2f4f7a 100%)"></div>
  <h3 class="get-title">WITH REMOTEHARBOR,<br>YOU GET TO:</h3>
  <div class="get-rule"></div>
  <ul class="benefits">
    <li><svg width="15" height="15" viewBox="0 0 16 16"><circle cx="8" cy="8" r="8" fill="#0f62c9"/><path d="M4.5 8.2 7 10.6 11.6 5.8" fill="none" stroke="#fff" stroke-width="2"/></svg>Work from the comfort of your home</li>
    <li><svg width="15" height="15" viewBox="0 0 16 16"><circle cx="8" cy="8" r="8" fill="#0f62c9"/><path d="M4.5 8.2 7 10.6 11.6 5.8" fill="none" stroke="#fff" stroke-width="2"/></svg>Have a competitive and steady income</li>
    <li><svg width="15" height="15" viewBox="0 0 16 16"><circle cx="8" cy="8" r="8" fill="#0f62c9"/><path d="M4.5 8.2 7 10.6 11.6 5.8" fill="none" stroke="#fff" stroke-width="2"/></svg>Achieve work-life balance</li>
    <li><svg width="15" height="15" viewBox="0 0 16 16"><circle cx="8" cy="8" r="8" fill="#0f62c9"/><path d="M4.5 8.2 7 10.6 11.6 5.8" fill="none" stroke="#fff" stroke-width="2"/></svg>Learn new skills for free</li>
    <li><svg width="15" height="15" viewBox="0 0 16 16"><circle cx="8" cy="8" r="8" fill="#0f62c9"/><path d="M4.5 8.2 7 10.6 11.6 5.8" fill="none" stroke="#fff" stroke-width="2"/></svg>Work with a dedicated team who can provide you with HR, payroll, IT, and training assistance 24/7!</li>
  </ul>
</section>

<section class="va-band">
  <h2 class="sec-title">WHO ARE OUR VIRTUAL ASSISTANTS?</h2>
  <div class="rule"></div>
  <div class="va-copy">
    <p>We have VAs from all over the Philippines.</p>
    <p>Our VA pool is composed of highly dedicated people armed with the right set of skills clients are looking for in a virtual assistant. We hire VAs of varying work experience and skill levels, and we help our VAs improve their skills so that they can get the jobs and clients they want.</p>
    <p>RemoteHarbor accepts VAs in a variety of niches. Currently, our VAs belongs to one or more of the following groups: Administrative VAs, eCommerce VAs, and Specialist VAs.</p>
    <p>Are you ready to join the team? To start the application process, please click on the button below.</p>
  </div>
  <a class="btn-outline">REQUEST HERE</a>
  <div class="va-art" role="img" aria-label="Illustration of a virtual assistant with a headset working at a laptop, with a chat bubble, clouds and city skyline"></div>
</section>

<section class="why">
  <h2 class="sec-title">WHY WORK FOR REMOTEHARBOR?</h2>
  <div class="rule"></div>
  <div class="pill active" style="left:119px;top:226px">COMPETITIVE HOURLY RATES</div>
  <div class="pill" style="left:119px;top:285px">FLEXIBLE HOURS</div>
  <div class="pill" style="left:119px;top:346px">FLEXIBLE SCHEDULE</div>
  <div class="pill" style="left:119px;top:406px">WEEKLY PAYOUT VIA PAYSTREAM</div>
  <div class="pill" style="left:119px;top:467px">PAYSTREAM FEES COVERED</div>
  <div class="pill" style="left:762px;top:226px">FREE TRAINING &amp; UPSKILLING</div>
  <div class="pill" style="left:762px;top:285px">NO PLACEMENT OR PROCESSING FEE</div>
  <div class="pill" style="left:762px;top:346px">WORK FROM HOME</div>
  <div class="pill" style="left:762px;top:406px">PAYROLL PROCESSING</div>
  <div class="pill" style="left:762px;top:467px">VARIOUS POSITIONS AVAILABLE</div>
  <div class="pill center" style="top:543px">CONTINUOUS RE-ASSIGNMENT TO CLIENTS</div>
  <div class="why-dial">
    <svg width="290" height="290" viewBox="0 0 290 290" aria-hidden="true">
      <circle cx="145" cy="145" r="140" fill="#232323"/>
      <path d="M145 5 A140 140 0 0 0 145 285 L145 270 A125 125 0 0 1 145 20Z" fill="#0f62c9"/>
      <circle cx="140" cy="148" r="128" fill="#0f62c9"/>
      <circle cx="147" cy="146" r="124" fill="#ffffff"/>
      <circle cx="145" cy="90" r="21" fill="none" stroke="#0f62c9" stroke-width="4"/>
      <text x="145" y="99" text-anchor="middle" font-family="Montserrat,sans-serif" font-weight="800" font-size="24" fill="#0f62c9">$</text>
    </svg>
    <p>We offer competitive rates based on your years of experience and skill proficiency.</p>
  </div>
</section>

<section class="testimonials">
  <h2 class="sec-title" style="top:2841px">TESTIMONIALS</h2>
  <div class="rule" style="top:2891px"></div>
  <article class="test-card" style="left:146px;width:273px">
    <div class="quote">“</div>
    <p>"Lorem ipsum dolor sit amet, consectet ur adipiscing elit, sed do eiusmod tempor incididunt ut labore et dolore magna aiq uaenim ad minim venia elited</p>
    <h4>- CASEY MORENO</h4>
  </article>
  <article class="test-card featured" style="left:446px;width:315px">
    <div class="quote">“</div>
    <p>"Lorem ipsum dolor sit amet, consectet ur adipiscing elit, sed do eiusmod tempor incididunt ut labore et dolore magna aiq uaenim ad minim venia elited</p>
    <h4>- CASEY MORENO</h4>
  </article>
  <article class="test-card" style="left:782px;width:272px">
    <div class="quote">“</div>
    <p>"Lorem ipsum dolor sit amet, consectet ur adipiscing elit, sed do eiusmod tempor incididunt ut labore et dolore magna aiq uaenim ad minim venia elited</p>
    <h4>- CASEY MORENO</h4>
  </article>
  <div class="dots"><span class="on"></span><span></span><span></span><span></span><span></span></div>
</section>

<footer class="footer">
  <svg class="abs" style="left:0;top:0" width="1200" height="369" viewBox="0 0 1200 369" preserveAspectRatio="none" aria-hidden="true">
    <path d="M0 40 Q600 -30 1200 60 L1200 369 L0 369Z" fill="#232323"/>
    <path d="M0 110 Q560 20 1200 80 L1200 369 L0 369Z" fill="#0f62c9"/>
    <path d="M380 70 Q800 40 1200 120 L1200 132 Q800 58 380 70Z" fill="#ffffff"/>
  </svg>
  <div class="brand-name">REMOTE<br>HARBOR</div>
  <ul class="foot-links" style="left:496px"><li>Home</li><li>About Us</li><li>Services offered</li><li>Pricing</li></ul>
  <ul class="foot-links" style="left:687px"><li>Testimonials</li><li>FAQs</li><li>Contact Us</li><li>Blog</li></ul>
  <a class="btn-outline" style="top:160px">GET STARTED</a>
  <a class="btn-outline" style="top:212px">SIGN IN</a>
  <div class="foot-rule"></div>
  <p class="copyright">Copyright 2020 All Rights Reserved I Terms of Use I Privacy Policy</p>
  <div class="social" aria-label="Social links"><span></span><span></span><span></span></div>
</footer>

</body>
</html>
```